Garlic Farm for Farm Sales/Restaurant sales

Need a professional, but appealing to agriculture world. We are selling 27 kinds of Organic Garlic from a farm in Simla,CO. I have uploaded logo and business information-we are going to need a template, because I will need to use it for four separate people.
-We are trying to appeal to Farm to table restaurants
-As well as growers/farmers

Target Market(s)

Agriculture Sales/Restaurants-Organic

Industry/Entity Type

Agriculture

Contact Information for Business Card

Want it to look more unique then your average kelto stock card- I want it to look amazing

Font styles to use
Sans Serif

Colors
0455a3
ec1f27
fbed22
ffffff

Requirements
Must have
• Just be creative
Nice to have
• Colorful
Should not have
• plain

```html
<!DOCTYPE html>
<html lang="en">
<head>
<meta charset="utf-8">
<title>Peakridge Garlic Co — Business Card</title>
<link rel="stylesheet" href="https://fonts.googleapis.com/css2?family=Open+Sans:wght@400;600&display=swap">
<style>
  :root {
    --stage: #f1efee;
    --coral: #cf4b40;
    --crimson: #c0102c;
    --navy: #0e2d5e;
    --ink-navy: #1c2b5a;
    --paper: #e8e4e4;
    --white: #ffffff;
  }
  * { margin: 0; padding: 0; box-sizing: border-box; }
  html, body {
    width: 1200px; height: 900px; overflow: hidden;
    background: var(--stage);
    font-family: "Open Sans", Arial, sans-serif;
  }
  .canvas { position: relative; width: 1200px; height: 900px; }

  .card { position: absolute; overflow: hidden; box-shadow: 0 6px 18px rgba(0,0,0,.15); }

  /* Front card */
  .card-front {
    left: 78px; top: 35px; width: 587px; height: 362px;
    background: var(--coral); color: var(--white);
  }
  .front-band {
    position: absolute; right: 0; top: 0; width: 120px; height: 100%;
    background: var(--navy);
  }
  .front-mark {
    position: absolute; left: 245px; top: 5px; width: 340px; height: 340px;
    border-radius: 50%; background: var(--crimson);
    display: flex; align-items: center; justify-content: center;
  }
  .front-brand {
    font-weight: 600; font-size: 24px; line-height: 32px;
    color: var(--white); text-align: center;
  }
  .person { position: absolute; left: 29px; top: 35px; }
  .person-name { font-weight: 600; font-size: 19px; line-height: 24px; }
  .person-title { font-size: 15px; line-height: 22px; }
  .address { position: absolute; left: 28px; top: 182px; font-size: 15px; line-height: 25px; }
  .contacts { position: absolute; left: 28px; top: 244px; list-style: none; font-size: 15px; line-height: 21.5px; }
  .contacts li { display: flex; align-items: center; gap: 8px; }
  .contacts svg { width: 11px; height: 11px; fill: var(--white); flex: none; }

  /* Back card */
  .card-back {
    left: 388px; top: 505px; width: 567px; height: 352px;
    background: var(--paper);
  }
  .back-mark {
    position: absolute; left: 222px; top: 72px; width: 120px; height: 120px;
    border-radius: 50%; background: var(--crimson);
  }
  .back-brand {
    position: absolute; left: 0; top: 200px; width: 100%;
    text-align: center; font-weight: 600; font-size: 34px; line-height: 46px; color: var(--ink-navy);
  }
</style>
</head>
<body>
<main class="canvas">

  <section class="card card-front">
    <div class="front-band"></div>
    <div class="front-mark">
      <p class="front-brand">Peakridge<br>Garlic Co</p>
    </div>

    <div class="person">
      <p class="person-name">Dana Whitlock</p>
      <p class="person-title">Managing Director</p>
    </div>

    <p class="address">4410 Prairie Road,<br>Simla, CO 80835</p>

    <ul class="contacts">
      <li><svg viewBox="0 0 12 12"><path d="M2 1h2.5l1 3-1.5 1a6 6 0 0 0 3 3l1-1.5 3 1V10a1 1 0 0 1-1 1A9 9 0 0 1 1 2a1 1 0 0 1 1-1z"/></svg>(719) 555 0142</li>
      <li><svg viewBox="0 0 12 12"><path d="M3 1h6v3H3zM1 5h10v5H9v1H3v-1H1zm3 3v2h4V8z"/></svg>(719) 5550143</li>
      <li><svg viewBox="0 0 12 12"><path d="M1 2h10v8H1zm1 1v.5l4 3 4-3V3z"/></svg>hello@peakridgegarlic.com</li>
      <li><svg viewBox="0 0 12 12"><path d="M5 7 7 5M4.5 5.5 2.5 7.5a1.8 1.8 0 0 0 2 2l2-2M7.5 6.5l2-2a1.8 1.8 0 0 0-2-2l-2 2" stroke="#fff" stroke-width="1.3" fill="none"/></svg>www.peakridgegarlic.com</li>
    </ul>
  </section>

  <section class="card card-back">
    <div class="back-mark"></div>
    <p class="back-brand">Peakridge Garlic Co</p>
  </section>

</main>
</body>
</html>
```